Corporate Design für Hausverwalterin und Immobilienvermarktung
Zielgruppe
Hausverwalterin und Immobilienvermarktung
Aufgabenstellung
wir sind im Immobiliensektor unterwegs und das Design soll edel und hochwertig sein

```html
<!DOCTYPE html>
<html lang="de">
<head>
<meta charset="utf-8">
<title>Veltor Immobilien – Geschäftsausstattung</title>
<link href="https://fonts.googleapis.com/css2?family=Roboto+Condensed:wght@400;500&family=Arimo:wght@400&display=swap" rel="stylesheet">
<style>
  :root {
    --bg: #f0f0ec;
    --navy: #162d44;
    --gold: #c9a862;
    --white: #ffffff;
    --paper-line: #eeeeee;
    --ink: #444a52;
    --ghost: #e4e6e9;
    --window: #e5e5e5;
  }
  * { margin: 0; padding: 0; box-sizing: border-box; }
  html, body { width: 1200px; height: 1200px; overflow: hidden; background: var(--bg); }
  body { position: relative; font-family: "Roboto Condensed", sans-serif; }

  .card {
    position: absolute; left: 82px; width: 457px; height: 261px;
    background: var(--navy); overflow: hidden;
  }
  .card--front { top: 316px; }
  .card--back { top: 628px; }
  .card__bands { position: absolute; left: 0; bottom: 0; width: 457px; height: 19px; }

  .brand-name {
    font-family: "Roboto Condensed", sans-serif; font-weight: 500;
    color: var(--gold); white-space: nowrap; display: flex; align-items: center;
  }
  .brand-name__dot { display: inline-block; background: currentColor; }

  .card--front .brand-name {
    position: absolute; left: 0; right: 0; top: 108px; justify-content: center;
    font-size: 30px; gap: 12px;
  }
  .card--front .brand-name__dot { width: 12px; height: 12px; }

  .card--back .brand-name {
    position: absolute; left: 36px; top: 140px; font-size: 17px; color: var(--white); gap: 7px;
  }
  .card--back .brand-name__dot { width: 8px; height: 8px; }
  .card__divider { position: absolute; left: 182px; top: 48px; width: 1.5px; height: 158px; background: var(--white); }
  .card__text { position: absolute; left: 201px; top: 46px; color: var(--white); font-size: 9.6px; line-height: 13px; letter-spacing: 0.2px; }
  .card__intro p { margin: 0; }
  .card__services { list-style: none; margin-top: 14px; color: var(--gold); line-height: 13.6px; }
  .card__services li::before { content: "• "; }
  .card__contact { margin-top: 15px; line-height: 13px; }

  .letterhead {
    position: absolute; left: 636px; top: 116px; width: 486px; height: 683px; background: var(--white);
  }
  .letterhead__strip { position: absolute; right: 0; top: 0; width: 19px; height: 100%; background: var(--gold); }
  .letterhead .brand-name--head { position: absolute; left: 83px; top: 84px; font-size: 16px; gap: 6px; }
  .letterhead .brand-name--head .brand-name__dot { width: 7px; height: 7px; }
  .letterhead__contact { position: absolute; left: 299px; top: 98px; font-size: 8px; line-height: 11px; color: var(--ink); letter-spacing: 0.3px; }
  .letterhead__ghost {
    position: absolute; left: 0; right: 19px; top: 402px; justify-content: center;
    font-size: 40px; color: var(--ghost); gap: 14px;
  }
  .letterhead__ghost .brand-name__dot { width: 16px; height: 16px; }
  .letterhead__block { position: absolute; left: 0; bottom: 0; width: 15px; height: 80px; background: var(--navy); }
  .letterhead__footer { position: absolute; top: 634px; font-family: "Arimo", sans-serif; font-size: 5px; line-height: 6px; color: #666; }
  .letterhead__footer--legal { left: 38px; }
  .letterhead__footer--bank { left: 237px; top: 637px; }
  .letterhead__footer-rule { position: absolute; left: 211px; top: 632px; width: 1px; height: 26px; background: #888; }

  .envelope {
    position: absolute; left: 638px; top: 844px; width: 512px; height: 256px; background: var(--white);
  }
  .envelope__strip { position: absolute; right: 0; top: 0; width: 19px; height: 100%; background: var(--gold); }
  .envelope .brand-name { position: absolute; left: 96px; top: 72px; font-size: 14px; gap: 5px; }
  .envelope .brand-name__dot { width: 6px; height: 6px; }
  .envelope__window { position: absolute; left: 52px; top: 115px; width: 232px; height: 99px; background: var(--window); border-radius: 6px; }
</style>
</head>
<body>

  <section class="card card--front" aria-label="Visitenkarte Vorderseite">
    <div class="brand-name"><span class="brand-name__dot"></span>Veltor Immobilien</div>
    <svg class="card__bands" viewBox="0 0 457 19" aria-hidden="true">
      <polygon points="0,0 366,0 356,10 0,10" fill="var(--gold)"/>
      <polygon points="371,0 457,0 457,10 361,10" fill="var(--paper-line)"/>
    </svg>
  </section>

  <section class="card card--back" aria-label="Visitenkarte Rückseite">
    <div class="brand-name"><span class="brand-name__dot"></span>Veltor Immobilien</div>
    <div class="card__divider"></div>
    <div class="card__text">
      <div class="card__intro">
        <p>Ganzheitliche Immobilienbetreuung mit Strategie</p>
        <p>Als zertifizierte Hausverwalterin &amp; Immobilienmaklerin</p>
        <p>gemäß § 34c GewO verbinde ich klassische</p>
        <p>Verwaltung mit wertoptimierter Vermarktung</p>
      </div>
      <ul class="card__services">
        <li>Hausverwaltung: Rechtssicher &amp; entlastend.</li>
        <li>Asset Management: Strategische Ertragssteigerung.</li>
        <li>Verkauf: Marktgerecht &amp; professionell</li>
      </ul>
      <div class="card__contact">
        <p>Telefon: 0151 389 20 47</p>
        <p>E-Mail: info@veltor-immobilien.de</p>
        <p>Webseite: www.veltor-immobilien.de</p>
      </div>
    </div>
    <svg class="card__bands" viewBox="0 0 457 19" aria-hidden="true">
      <polygon points="0,0 366,0 356,10 0,10" fill="var(--gold)"/>
      <polygon points="371,0 457,0 457,10 361,10" fill="var(--paper-line)"/>
    </svg>
  </section>

  <section class="letterhead" aria-label="Briefbogen">
    <div class="brand-name brand-name--head"><span class="brand-name__dot"></span>Veltor Immobilien</div>
    <div class="letterhead__contact">
      <p>Telefon: 0151 389 20 47</p>
      <p>E-Mail: info@veltor-immobilien.de</p>
      <p>Webseite: www.veltor-immobilien.de</p>
    </div>
    <div class="brand-name letterhead__ghost"><span class="brand-name__dot"></span>Veltor Immobilien</div>
    <div class="letterhead__block"></div>
    <div class="letterhead__footer letterhead__footer--legal">
      <p>Persönlich haftende Gesellschafterin:</p>
      <p>KRM Handels- und Verwaltungs-GmbH, Sitz: Lindhorst/Nds.</p>
      <p>Registergericht: Amtsgericht Nordstadt – HRB 104233</p>
      <p>Geschäftsführerin: Marlene Hofstede</p>
    </div>
    <div class="letterhead__footer-rule"></div>
    <div class="letterhead__footer letterhead__footer--bank">
      <p>Genossenschaftsbank Nordland eG</p>
      <p>BIC: GENODEF1NRL</p>
      <p>IBAN: DE00 1234 5678 9012 3456 78</p>
    </div>
    <div class="letterhead__strip"></div>
  </section>

  <section class="envelope" aria-label="Briefumschlag">
    <div class="brand-name"><span class="brand-name__dot"></span>Veltor Immobilien</div>
    <div class="envelope__window"></div>
    <div class="envelope__strip"></div>
  </section>

</body>
</html>
```